Brand Identity Stationary Package

Hello I'm looking for a full branding package for my Property Management Company. I have a logo but looking to have the following
Business Card
Email signature
Facebook cover photo
Letterhead (word.doc)
#10 Envelope
Pocket Folder - link to 9x12 pocket folder design specs https://www.printorbit-example.ca/marketing-materials/presentation-folders
would like everything to match and be brand identifiable. The company looks after residential properties/apartments and some commercial properties. Attached is a zip of the files.
For Business Card
Name: Gareth Lindqvist
Position: Operations Manager
Number: 1 (555) 384-2917
Email: Gareth@harborkey-example.ca
Website: Harborkey-example.ca
Property Management

```html
<!DOCTYPE html>
<html lang="en">
<head>
<meta charset="utf-8">
<title>Harborkey Property Management – Pocket Folder</title>
<link rel="stylesheet" href="https://fonts.googleapis.com/css2?family=Montserrat:wght@500;700&family=Open+Sans:wght@400;600&display=swap">
<style>
  :root {
    --green: #84ad3c;
    --green-dark: #6c8f34;
    --ink: #1a1a1a;
    --paper: #ffffff;
    --paper-shade: #e6e6e6;
    --backdrop: #b9b7b8;
    --body-text: #333333;
  }
  * { margin: 0; padding: 0; box-sizing: border-box; }
  html, body { width: 982px; height: 1200px; overflow: hidden; }
  body {
    background: var(--backdrop);
    font-family: "Open Sans", sans-serif;
    position: relative;
  }
  .spread {
    position: absolute;
    left: 91px;
    width: 800px;
    height: 533px;
    display: flex;
    box-shadow: 0 14px 30px rgba(0,0,0,0.25);
  }
  .spread--outside { top: 30px; }
  .spread--inside { top: 607px; }
  .panel { position: relative; width: 400px; height: 533px; overflow: hidden; }

  /* wordmark */
  .wordmark { display: flex; align-items: center; gap: 7px; }
  .wordmark__square { width: 10px; height: 10px; background: var(--green); }
  .wordmark__name {
    font-family: "Montserrat", sans-serif;
    font-weight: 700;
    letter-spacing: 2px;
    color: var(--ink);
    text-transform: uppercase;
    line-height: 1;
  }
  .tagline {
    font-family: "Montserrat", sans-serif;
    font-weight: 500;
    text-transform: uppercase;
    color: var(--ink);
    letter-spacing: 5px;
  }

  /* outside back cover */
  .back-cover { background: linear-gradient(90deg, var(--green) 0%, var(--green-dark) 100%); }
  .back-cover .wordmark { position: absolute; top: 70px; left: 100px; }
  .back-cover .wordmark__name { font-size: 26px; color: var(--ink); }
  .back-cover .wordmark__square { background: var(--paper); }
  .back-cover .tagline { position: absolute; top: 104px; left: 102px; font-size: 7px; letter-spacing: 4px; }
  .back-cover__services {
    position: absolute; bottom: 82px; left: 0; right: 0; text-align: center;
    font-family: "Montserrat", sans-serif; font-weight: 700; font-size: 8px;
    color: var(--paper); text-transform: uppercase; line-height: 1.7;
  }
  .back-cover__rule { position: absolute; bottom: 62px; left: 60px; right: 40px; height: 1px; background: rgba(255,255,255,0.6); }
  .back-cover__contact {
    position: absolute; bottom: 38px; left: 0; right: 0;
    display: flex; justify-content: center; gap: 8px; align-items: center;
    color: var(--paper); font-size: 9.5px;
  }
  .contact-item { display: inline-flex; align-items: center; gap: 3px; }
  .contact-item svg { width: 9px; height: 9px; }

  /* outside front cover */
  .front-cover { background: linear-gradient(90deg, var(--paper-shade) 0%, var(--paper) 40%); }
  .front-cover .wordmark { position: absolute; top: 70px; left: 0; right: 0; justify-content: center; }
  .front-cover .wordmark__name { font-size: 38px; }
  .front-cover .tagline { position: absolute; top: 116px; left: 0; right: 0; text-align: center; font-size: 9px; letter-spacing: 7px; }
  .front-cover__band { position: absolute; bottom: 0; right: 0; width: 260px; height: 40px; }
  .front-cover__url {
    position: absolute; bottom: 12px; right: 40px;
    color: var(--paper); font-size: 11px;
  }

  /* inside */
  .inside-left { background: linear-gradient(90deg, var(--paper) 0%, var(--paper-shade) 60%, #bdbdbd 100%); }
  .inside-right { background: linear-gradient(90deg, #cfcfcf 0%, var(--paper) 25%); }
  .pocket { position: absolute; left: 0; bottom: 0; width: 400px; height: 200px; }

  .letterhead {
    position: absolute; top: 24px; left: 36px; width: 330px; height: 480px;
    background: var(--paper); box-shadow: 0 2px 8px rgba(0,0,0,0.18);
    padding: 22px 20px;
  }
  .letterhead .wordmark__name { font-size: 17px; }
  .letterhead .wordmark__square { width: 7px; height: 7px; }
  .letterhead .tagline { font-size: 5px; letter-spacing: 3px; margin-top: 3px; }
  .letterhead__sender { position: absolute; top: 18px; right: 20px; font-size: 6px; line-height: 1.5; color: var(--ink); }
  .letterhead__sender-name { color: var(--green); font-weight: 600; text-transform: uppercase; }
  .letterhead__sender .contact-item svg { width: 6px; height: 6px; }
  .letterhead__rule { height: 1px; background: var(--green); margin: 22px 0 26px; }
  .letterhead__recipient { font-size: 6px; line-height: 1.45; color: var(--body-text); margin-bottom: 6px; }
  .letterhead__body p { font-size: 6px; line-height: 1.5; color: var(--body-text); text-align: justify; margin-bottom: 7px; }
</style>
</head>
<body>

<section class="spread spread--outside">
  <div class="panel back-cover">
    <div class="wordmark"><span class="wordmark__name">Harborkey</span><span class="wordmark__square"></span></div>
    <div class="tagline">Property Management</div>
    <div class="back-cover__services">Tenants, and Landlords<br>Property Management</div>
    <div class="back-cover__rule"></div>
    <div class="back-cover__contact">
      <span class="contact-item">
        <svg viewBox="0 0 10 10"><path d="M1 3c0-1 1-2 2-2h4c1 0 2 1 2 2v1H7V3H3v1H1z M2 5h6l1 4H1z" fill="#fff"/></svg>
        1 (555) 384-2917
      </span>
      <span class="contact-item">
        <svg viewBox="0 0 10 10"><rect x="0.5" y="2" width="9" height="6" fill="#fff"/><path d="M0.5 2l4.5 3.5L9.5 2" stroke="#6c8f34" fill="none"/></svg>
        Gareth@harborkey-example.ca
      </span>
      <span class="contact-item">
        <svg viewBox="0 0 10 10"><circle cx="5" cy="5" r="4.3" fill="none" stroke="#fff"/><path d="M0.7 5h8.6M5 0.7c-2.5 2.5-2.5 6 0 8.6M5 0.7c2.5 2.5 2.5 6 0 8.6" stroke="#fff" fill="none" stroke-width="0.7"/></svg>
        Harborkey-example.ca
      </span>
    </div>
  </div>
  <div class="panel front-cover">
    <div class="wordmark"><span class="wordmark__name">Harborkey</span><span class="wordmark__square"></span></div>
    <div class="tagline">Property Management</div>
    <svg class="front-cover__band" viewBox="0 0 260 40" preserveAspectRatio="none"><polygon points="24,0 260,0 260,40 0,40" fill="var(--green)"/></svg>
    <div class="front-cover__url">www.Harborkey-example.ca</div>
  </div>
</section>

<section class="spread spread--inside">
  <div class="panel inside-left">
    <svg class="pocket" viewBox="0 0 400 200" preserveAspectRatio="none">
      <path d="M0 40 Q200 0 320 0 Q340 0 350 15 L400 200 L0 200 Z" fill="var(--green)"/>
    </svg>
  </div>
  <div class="panel inside-right">
    <article class="letterhead">
      <div class="wordmark"><span class="wordmark__name">Harborkey</span><span class="wordmark__square"></span></div>
      <div class="tagline">Property Management</div>
      <div class="letterhead__sender">
        <div class="letterhead__sender-name">Gareth Lindqvist</div>
        <div>Operations Manager</div>
        <div class="contact-item"><svg viewBox="0 0 10 10"><circle cx="5" cy="5" r="4" fill="var(--green)"/></svg>1 (555) 384-2917</div><br>
        <div class="contact-item"><svg viewBox="0 0 10 10"><rect x="1" y="2" width="8" height="6" fill="var(--green)"/></svg>Gareth@harborkey-example.ca</div><br>
        <div class="contact-item"><svg viewBox="0 0 10 10"><circle cx="5" cy="5" r="4" fill="var(--green)"/></svg>Harborkey-example.ca</div>
      </div>
      <div class="letterhead__rule"></div>
      <div class="letterhead__recipient">Mr/s<br>First Name and Last Name<br>Company Name<br>Address</div>
      <div class="letterhead__body">
        <p>Lorem ipsum dolor sit amet, consectetur adipiscing sed do eiusmod tempor incididunt labore et dolore magna aliqua. Ut enim ad minim veniam, quis nostrud exercitation ullamco laboris nisi ut aliquip ex ea commodo consequat.</p>
        <p>Lorem ipsum dolor sit amet, consectetur adipiscing sed do eiusmod tempor incididunt labore et dolore magna aliqua. Ut enim ad minim veniam, quis nostrud exercitation ullamco laboris nisi ut aliquip. Duis aute irure dolor in reprehenderit in voluptate velit esse.</p>
        <p>Lorem ipsum dolor sit amet, consectetur adipiscing sed do eiusmod tempor incididunt labore et dolore magna aliqua. Duis aute irure dolor in reprehenderit in voluptate velit esse cillum dolore eu fugiat nulla pariatur. Excepteur sint occaecat cupidatat non proident.</p>
        <p>Lorem ipsum dolor sit amet, consectetur adipiscing sed do eiusmod tempor incididunt labore et dolore magna aliqua. Ut enim Lorem ipsum dolor sit amet.</p>
        <p>Lorem ipsum dolor sit amet, consectetur adipiscing sed do eiusmod tempor incididunt labore et dolore magna aliqua. Ut enim ad minim veniam, quis nostrud exercitation ullamco laboris nisi ut aliquip.</p>
      </div>
    </article>
    <svg class="pocket" viewBox="0 0 400 200" preserveAspectRatio="none">
      <path d="M0 200 L30 50 Q34 36 50 34 L400 0 L400 200 Z" fill="var(--green)"/>
    </svg>
  </div>
</section>

</body>
</html>
```